BOLD & MINIMALIST DESIGN NEEDED

We want a very bold but minimalistic business card design that is impactful and utilizes both sides of the business card. Our current logo is included for your use.

We want bold fonts and good use of negative space. We don't want the logo to overpower the design.

Target Market(s)

Professionals who are building new commercial buildings.

Industry/Entity Type

Construction

Contact Information for Business Card

Name, Title, email, office phone, cell phone, website

Font styles to use
Serif
Sans Serif

Requirements
Must have
• Bold design!

```html
<!DOCTYPE html>
<html lang="en">
<head>
<meta charset="utf-8">
<title>Stonecrest Design + Build — Business Card</title>
<link rel="stylesheet" href="https://fonts.googleapis.com/css2?family=Montserrat:wght@400;500;600;800&display=swap">
<style>
  :root {
    --backdrop: #2a2a2a;
    --card: #0d0d0d;
    --green: #8cd63a;
    --green-light: #b6ec6e;
    --white: #ffffff;
    --silver: #c9c9c9;
    --text-font: "Montserrat", Arial, sans-serif;
  }
  * { box-sizing: border-box; margin: 0; padding: 0; }
  html, body { width: 1200px; height: 900px; overflow: hidden; }
  body {
    background: var(--backdrop);
    font-family: var(--text-font);
    position: relative;
  }
  .card {
    position: absolute;
    left: 250px;
    width: 700px;
    height: 400px;
    background: var(--card);
    border-radius: 28px;
    border-bottom: 8px solid var(--green);
    overflow: hidden;
  }
  .card--front { top: 40px; }
  .card--back { top: 460px; }

  .brand-name {
    position: absolute;
    left: 0; right: 0;
    text-align: center;
    font-weight: 800;
    text-transform: uppercase;
    color: var(--white);
    letter-spacing: 1px;
  }
  .card--front .brand-name { top: 70px; font-size: 40px; }
  .card--back .brand-name { top: 170px; font-size: 46px; color: var(--silver); }

  .person {
    position: absolute;
    top: 170px; left: 0; right: 0;
    text-align: center;
  }
  .person__name {
    font-weight: 600;
    font-size: 28px;
    color: var(--green);
    text-transform: uppercase;
    line-height: 1.1;
  }
  .person__title {
    font-weight: 500;
    font-size: 19px;
    color: var(--white);
  }

  .contact-rule {
    position: absolute;
    top: 268px; left: 0; right: 0;
    height: 2px;
    background: var(--green);
  }
  .contact {
    position: absolute;
    top: 290px; left: 0; right: 0;
    display: flex;
    justify-content: center;
    font-size: 19px;
    color: var(--white);
    font-weight: 400;
    line-height: 32px;
  }
  .contact__col { padding: 0 22px; }
  .contact__col--web { text-align: right; border-right: 2px solid var(--green); }
  .contact__row { display: flex; align-items: center; gap: 10px; }
  .contact__col--web .contact__row { justify-content: flex-end; }
  .icon { width: 20px; height: 20px; flex: none; }
</style>
</head>
<body>

<section class="card card--front" aria-label="Card front">
  <p class="brand-name">Stonecrest Design + Build</p>

  <div class="person">
    <p class="person__name">Daniel Reeves</p>
    <p class="person__title">Managing Director</p>
  </div>

  <div class="contact-rule"></div>

  <div class="contact">
    <div class="contact__col contact__col--web">
      <p class="contact__row">info@stonecrestbuild.com
        <svg class="icon" viewBox="0 0 20 20" fill="none" stroke="var(--green)" stroke-width="2"><rect x="2" y="4" width="16" height="12"/><path d="M2 4l8 7 8-7"/></svg>
      </p>
      <p class="contact__row">www.stonecrestbuild.com
        <svg class="icon" viewBox="0 0 20 20" fill="none" stroke="var(--green)" stroke-width="1.6"><circle cx="10" cy="10" r="8"/><ellipse cx="10" cy="10" rx="3.5" ry="8"/><path d="M2 10h16M4 5.5h12M4 14.5h12"/></svg>
      </p>
    </div>
    <div class="contact__col contact__col--phone">
      <p class="contact__row">
        <svg class="icon" viewBox="0 0 20 20" fill="var(--green)"><path d="M5 2l3 3-2 2.5c1 2 2.5 3.5 4.5 4.5L13 10l3 3-2 3c-6 0-12-6-12-12z"/></svg>
        044-555 010 200
      </p>
      <p class="contact__row">
        <svg class="icon" viewBox="0 0 20 20" fill="none" stroke="var(--green)" stroke-width="2"><rect x="5" y="2" width="10" height="16" rx="2"/><path d="M9 15h2"/></svg>
        044-555 010 300
      </p>
    </div>
  </div>
</section>

<section class="card card--back" aria-label="Card back">
  <p class="brand-name">Stonecrest Design + Build</p>
</section>

</body>
</html>
```